Zielgruppe
Wir sind ein Business Center und vermieten Büro- und Konferenzräume. Wir richten uns an Unternehmen unterschiedlichster Branchen: Freelancer ohne eigenes Büro oder auch große Unternehmen, welche keine eigene freien Vakanzen haben, z. B. für Vorstellungsgespräche.
Aufgabenstellung
Flyer Din Lang, quer, gebunden an der kurzen Seite. 8 Seiten, inkl. Vorder- und Rückseite. Bitte kein Wickelfalz oder ähnliches, sondern eine Broschüre, gebunden mit Klammerheftung!!!
Frisches helles Design, ohne Schnörkel. Bilder mit etwas Text, dazu eine Seite über uns. Rückseite Kontaktdaten. Je eine Doppelseite für Konferenzraumvermietung und eine Doppelseite für Büroraum auf Zeit, eine Doppelseite für unsere weitere Leistungen, Telefonservice (Anrufannahme im namen unserer Kunden).
Unsere Räume sind sehr repräsentativ und modern eingerichtet mit hellen Designermöbeln. Das soll auch in der Broschüre klar werden.

```html
<!DOCTYPE html>
<html lang="de">
<head>
<meta charset="utf-8">
<title>NORVENTA Broschüre 2018</title>
<link href="https://fonts.googleapis.com/css2?family=Open+Sans:wght@400;600;700&display=swap" rel="stylesheet">
<style>
:root{
  --green:#8db30b;
  --green-dark:#7a9c08;
  --ink:#3b3d40;
  --muted:#6a6d72;
  --paper:#ffffff;
  --stage:#e4e7ec;
  --photo-warm:#cfc6b6;
  --photo-cool:#d9dde2;
  --photo-dark:#4c5257;
}
*{box-sizing:border-box;margin:0;padding:0}
html,body{width:1200px;height:3277px;overflow:hidden}
body{background:var(--stage);font-family:"Open Sans",Arial,sans-serif;color:var(--ink);position:relative}
.abs{position:absolute}
.page-cover{position:absolute;width:627px;height:448px;background:var(--paper);overflow:hidden}
.spread{position:absolute;width:1161px;height:414px;background:var(--paper);overflow:hidden}
.logo{position:absolute;display:flex;align-items:center;gap:8px;font-weight:600;color:var(--ink);letter-spacing:.5px}
.logo .mark{width:14px;height:14px;background:var(--green)}
.year{position:absolute;text-align:right;font-size:8px;line-height:1.15;color:var(--ink)}
.year b{display:block;font-size:22px;color:var(--green);font-weight:700;line-height:1}
.photo{position:absolute}
.band{position:absolute;background:var(--green)}
.cover-title{color:#fff;font-size:27px;line-height:.92;font-weight:400;letter-spacing:.5px}
.lead{position:absolute;font-size:6.5px;line-height:1.3;color:var(--muted)}
.url{position:absolute;left:0;right:0;text-align:center;font-size:10px;font-weight:700;color:var(--ink)}
.tab{position:absolute;background:var(--green);color:#fff;font-size:15px;padding-left:30px;display:flex;align-items:center}
.box{position:absolute;background:var(--green);color:#fff;font-size:6px;line-height:1.45}
.box h3{font-weight:400;font-size:18px;margin-bottom:14px}
.box p{margin-bottom:8px}
.ticks{list-style:none}
.ticks li{position:relative;padding-left:10px;margin-bottom:3px}
.ticks li::before{content:"➔";position:absolute;left:0;font-size:5.5px}
.faq dt{font-weight:700;margin-top:6px}
.faq dd{margin-bottom:2px}
.small-dots{list-style:none}
.small-dots li{position:relative;padding-left:10px;margin-bottom:7px}
.small-dots li::before{content:"";position:absolute;left:0;top:2px;width:4px;height:4px;border:1px solid #fff;border-radius:50%}
.small-dots b{display:block;font-weight:700}
.quote{position:absolute;color:#fff;font-size:6.2px;line-height:1.45;text-align:center}
.quote cite{display:block;font-style:normal;font-weight:700;font-size:7.5px;margin-top:8px}
.quote cite span{font-weight:400;font-size:5.5px}
.avatar{position:absolute;width:38px;height:38px;border-radius:50%;background:#bfc3c7;border:2px solid #fff}
.conf-faq{position:absolute;font-size:6.3px;line-height:1.45;color:var(--ink)}
.conf-faq dt{color:var(--green);font-weight:700;margin-top:5px;padding-left:10px;position:relative}
.conf-faq dt::before{content:"➔";position:absolute;left:0}
.conf-faq dd{padding-left:10px}
.conf-faq.right dt,.conf-faq.right dd{padding-left:0}
.conf-faq.right dt::before{content:none}
.contact{position:absolute;color:#fff;font-size:6.5px;line-height:1.35}
.contact b{font-weight:600;display:block}
</style>
</head>
<body>

<!-- Cover -->
<section class="page-cover" style="left:271px;top:74px" aria-label="Titelseite">
  <div class="logo" style="left:47px;top:52px;font-size:20px"><span class="mark"></span>NORVENTA</div>
  <div class="year" style="right:36px;top:36px"><b>2018</b>DIE MODERNE<br>ART DES MIETENS</div>
  <div class="photo" role="img" aria-label="Fassade eines modernen Bürogebäudes" style="left:0;top:127px;width:315px;height:194px;background:linear-gradient(90deg,#e6dfd3,var(--photo-warm) 60%,#b9ae9c);clip-path:polygon(0 0,100% 0,72% 100%,0 100%)"></div>
  <div class="band" style="left:193px;top:168px;width:434px;height:110px;clip-path:polygon(12% 0,100% 0,100% 100%,0 100%);display:flex;align-items:center;padding-left:100px">
    <h1 class="cover-title">NEUE MAßSTÄBE<br>SETZEN</h1>
  </div>
  <p class="lead" style="left:385px;top:294px;width:210px">Unser modernes Business Center bietet mehr als ein reines Callcenter. Anrufannahme, hochwertigste Mietbüros und ein stylischer Konferenzraum</p>
  <p class="url" style="top:381px">www.buero-norventa.de</p>
</section>

<!-- Spread: Willkommen / Inbound -->
<section class="spread" style="left:20px;top:687px" aria-label="Willkommen und Telefonservice">
  <h2 class="abs" style="left:53px;top:52px;font-size:25px;font-weight:400;letter-spacing:1px">WILLKOMMEN</h2>
  <div class="band" style="left:253px;top:57px;width:325px;height:23px"></div>
  <div class="box" style="left:30px;top:104px;width:548px;height:223px;padding:20px 40px 0 72px">
    <h3>Viel mehr als ein Callcenter</h3>
    <p>Im Gründungsjahr 2003 wurde die Idee zu einem Schreibbüro geboren: Briefe verfassen, Mailings versenden, Daten erfassen – das war der Grundgedanke.</p>
    <p>Nach den ersten Jahren entwickelte sich das Unternehmen in eine neue Richtung und der Bereich Telefonservice wurde etabliert.</p>
    <p>Seit mehr als 15 Jahren leisten wir unseren Beitrag für einen optimalen Kundenservice am Telefon. Freundliche Mitarbeiterinnen und Mitarbeiter geben täglich ihr Bestes für viele namhafte Kunden aus ganz Europa. Hierbei legen wir größten Wert auf gut ausgebildete Mitarbeiter sowie hochwertigste Technik. Daher hat sich NORVENTA 2012, nach einer Testphase, für moderne Internettelefonie entschieden und telefoniert seitdem zuverlässig in bester Qualität.</p>
  </div>
  <div class="band" style="left:0;top:350px;width:253px;height:18px"></div>

  <div class="photo" role="img" aria-label="Arzt im weißen Kittel mit Stethoskop und Krawatte" style="left:578px;top:45px;width:557px;height:308px;background:linear-gradient(120deg,#f1f2f4,#dfe2e6 55%,#c9ced4)"></div>
  <div class="band" style="left:602px;top:57px;width:176px;height:23px;color:#fff;font-size:8.5px;display:flex;align-items:center;padding-left:10px;letter-spacing:.5px">INBOUND / OUTBOUND</div>
  <div class="box" style="left:578px;top:83px;width:265px;height:244px;padding:12px 14px 0 14px;font-size:5.3px;line-height:1.35">
    <ul class="small-dots">
      <li><b>Telefonservice SimpleCall</b>Ihre Anrufer werden begeistert sein, dass Sie ab sofort durchgängig erreichbar sind. Verschieben Sie zukünftig auf einen persönlichen Anrufbeantworter oder die Rufumleitung auf Ihr Mobiltelefon.</li>
      <li><b>Telefonservice PraxisCall</b>Seit 2013 bietet NORVENTA den speziell auf Arztpraxen ausgerichteten Telefonservice an. Damit steht Ihnen ein individuell angepasster Tarif für diese Kundengruppe zur Verfügung.</li>
      <li><b>Wir qualifizieren Ihre Leads</b>Sie planen eine neue Marketing-Maßnahme für Ihre Produkte und Leistungen? Unser Outbound-Team fordert Ihre Interessenten auf und generiert Leads, die Sie direkt nutzen.</li>
      <li><b>Telefonanlagen Beispiele</b>Überzeugen Sie sich von der Qualität unserer Ansagen und hören Sie in unsere Beispielansagen rein. Ihre eigene Ansage wird individuell erstellt.</li>
    </ul>
  </div>
</section>

<!-- Spread: Büroanmietung -->
<section class="spread" style="left:22px;top:1401px" aria-label="Büroanmietung in Düsseldorf">
  <div class="photo" role="img" aria-label="Heller Schreibtisch mit Designerlampe, Laptop und Bürostuhl" style="left:9px;top:45px;width:554px;height:315px;background:linear-gradient(160deg,#f3f3f2,#e2e1dd 55%,#c8c2b6)"></div>
  <div class="tab" style="left:0;top:56px;width:253px;height:26px">Büroanmietung in Düsseldorf</div>
  <div class="box" style="left:0;top:106px;width:280px;height:224px;padding:16px 20px 0 32px">
    <p>Nach Vertragsunterzeichnung können Sie sofort einziehen: kein Umbau, keine Renovierung und wenn Sie wünschen, können Sie das Mietverhältnis kurzfristig wieder kündigen. Soviel Flexibilität erhalten Sie nur bei uns!</p>
    <ul class="ticks" style="margin-top:22px">
      <li>Zugang 24/7</li>
      <li>persönlicher Empfang</li>
      <li>ab 15qm</li>
      <li>eigenes Firmenschild</li>
      <li>wöchentliche Reinigung inklusive</li>
      <li>kostenfreies Hochgeschwindigkeits-Internetzugang</li>
      <li>große Schreibtische</li>
      <li>auf Wunsch inkl. Anrufannahme durch unser geschultes Personal</li>
      <li>optionale Anmietung eines Konferenzraumes mit bis zu 10 Plätzen</li>
      <li>Mitbenutzung der sanitären Einrichtungen und der Küche</li>
    </ul>
  </div>

  <div class="photo" role="img" aria-label="Collage aus hellen möblierten Büroräumen und Loungebereich" style="left:612px;top:45px;width:280px;height:315px;background:linear-gradient(135deg,#e7e4de,#cbb79a 50%,#8f8a83)"></div>
  <div class="band" style="left:812px;top:45px;width:289px;height:11px;background:#b9cf6a"></div>
  <div class="tab" style="left:812px;top:56px;width:349px;height:26px;padding-left:12px">Büroanmietung FAQ</div>
  <div class="box" style="left:892px;top:107px;width:269px;height:253px;padding:12px 12px 0 14px;font-size:5.6px;line-height:1.35">
    <dl class="faq ticks">
      <dt>➔ Welche Vertragslaufzeiten gibt es?</dt><dd>Der Mietvertrag läuft auf unbestimmte Zeit und ist mit einer Kündigungsfrist von 3 Monaten kündbar.</dd>
      <dt>➔ Kann ich auch am Wochenende in mein Büro?</dt><dd>Ja, Sie erhalten einen Hausschlüssel sowie einen Schlüssel für Ihr privates Büro. Der Zugang ist somit 24/7 möglich.</dd>
      <dt>➔ Wie beauftrage ich das Büro?</dt><dd>Bitte rufen Sie uns an unter 0800 1 234 567 und wir senden Ihnen den Mietvertrag zu. Nach Unterzeichnung können Sie Ihr Büro beziehen.</dd>
      <dt>➔ Was bedeutet Anrufannahme?</dt><dd>Auf Wunsch können wir Ihnen eine Düsseldorfer Rufnummer zur Verfügung stellen und unsere Agenten nehmen Ihre Anrufe entgegen.</dd>
      <dt>➔ Kann ich Getränke erwerben?</dt><dd>Ja, selbstverständlich halten wir Getränke für unsere Mieter bereit, welche Sie am Empfang erwerben können.</dd>
      <dt>➔ Wird mein Büro gereinigt?</dt><dd>Ja, Ihr Büro wird von unserer Reinigungsfachkraft zweimal pro Woche gereinigt.</dd>
    </dl>
  </div>
</section>

<!-- Spread: Konferenzraum -->
<section class="spread" style="left:22px;top:2093px" aria-label="Konferenzraum anmieten">
  <div class="photo" role="img" aria-label="Heller Konferenzraum mit weißem Tisch und Designerstühlen" style="left:93px;top:41px;width:484px;height:322px;background:linear-gradient(150deg,#f2f2f1,#e3e2df 55%,#b9a89a)"></div>
  <div class="tab" style="left:34px;top:54px;width:246px;height:26px;padding-left:8px">Konferenzraum anmieten</div>
  <div class="box" style="left:34px;top:105px;width:246px;height:226px;padding:18px 16px 0 12px">
    <p>Nutzen Sie unsere modernen Konferenz- und Tagungsräume für Meetings, Präsentationen, Gespräche oder Schulungen. Unsere hellen, stylischen Räume werden auch Sie faszinieren. Präsentieren Sie sich vor Ihren Geschäftspartnern an einem tollen Ort. Unser Team erfüllt all Ihre Wünsche – vom leckeren Cappuccino bis zu raffinierten Canapés.</p>
    <ul class="ticks" style="margin-top:12px">
      <li>bis zu 10 Teilnehmer</li>
      <li>bekannte Location im Lindenhaus (Autohaus)</li>
      <li>persönlicher Empfang &amp; Betreuung</li>
      <li>55 Zoll 4k Fernseher</li>
      <li>Streaming-Box</li>
      <li>Cast-Stick</li>
      <li>Konferenztelefon</li>
      <li>großes Whiteboard</li>
      <li>Flipchart</li>
      <li>Tiefgarage</li>
      <li>auch auf Raumbörse buchbar</li>
    </ul>
  </div>

  <div class="band" style="left:919px;top:26px;width:242px;height:10px"></div>
  <div class="photo" role="img" aria-label="Zufriedene Kunden mit erhobenem Daumen" style="left:587px;top:36px;width:552px;height:193px;background:linear-gradient(90deg,var(--photo-dark),#5d6368 50%,#474c51)"></div>
  <div class="tab" style="left:823px;top:46px;width:251px;height:24px;font-size:15px;padding-left:20px">Das sagen unsere Kunden</div>
  <div class="avatar" role="img" aria-label="Porträtfoto Kunde" style="left:744px;top:84px"></div>
  <div class="avatar" role="img" aria-label="Porträtfoto Kunde" style="left:987px;top:84px"></div>
  <div class="quote" style="left:640px;top:132px;width:240px">„Ich nutze den Telefonservice von NORVENTA seit ca. einem halben Jahr und bin sehr zufrieden. Wichtig sind mir insbesondere, dass Anrufe zuverlässig und rasch entgegen genommen werden können, sowie die Freundlichkeit der Mitarbeiter. In beiden Punkten wurden meine Erwartungen voll erfüllt.“<cite>- Dr. med. Jonas Reiter <span>www.praxis-reiter.de</span></cite></div>
  <div class="quote" style="left:890px;top:132px;width:240px">„Seit mehr als 2 Jahren nutze ich den Telefonservice von NORVENTA. Mich überzeugt nach wie vor die absolut professionelle Leistung, verbunden mit dem besten Preis-Leistungsverhältnis. Ich freue mich, dass ich NORVENTA gefunden habe!“<cite>- Martin Kessler, Kanzlei Brandt <span>www.kanzlei-brandt.de</span></cite></div>
  <div class="band" style="left:587px;top:229px;width:237px;height:19px;color:#fff;font-size:10.5px;display:flex;align-items:center;padding-left:34px">Konferenzraumvermietung FAQ</div>
  <svg class="abs" style="left:1061px;top:233px" width="56" height="56" viewBox="0 0 56 56" role="img" aria-label="Auszeichnung"><circle cx="28" cy="28" r="26" fill="#8a2f86"/><circle cx="28" cy="28" r="18" fill="none" stroke="#fff" stroke-width="1.5"/></svg>
  <dl class="conf-faq" style="left:604px;top:247px;width:275px">
    <dt>Werden meine Gäste begrüßt?</dt><dd>Ja, unsere freundlichen Damen begrüßen Ihre Besucher und führen Sie in den Besprechungsraum.</dd>
    <dt>Kann ich mein Notebook an den Bildschirm anschließen?</dt><dd>Ja, unser moderner Konferenzraum bietet für alle gängigen Systeme Lösungen: Streaming-Box, Cast-Stick, LAN oder WLAN.</dd>
    <dt>Gibt es auch einen Beamer?</dt><dd>Ja, auf Wunsch stellen wir auch einen Beamer mit Leinwand zur Verfügung. Wir empfehlen aber immer unseren großen Bildschirm mit 4k für brillante Präsentationen.</dd>
  </dl>
  <dl class="conf-faq right" style="left:901px;top:293px;width:240px">
    <dt>Werden Getränke gereicht?</dt><dd>Selbstverständlich stellen wir Ihnen und Ihren Gästen gerne Wasser, Cola usw. bereit. Uns unser leckerer Kaffee wird Ihnen schmecken.</dd>
    <dt>Kann ich ein Catering ordern?</dt><dd>Sollte Ihr Meeting einmal länger dauern, können Sie gerne mit uns ein individuelles Catering planen: vom klassischen Mettbrötchen bis hin zu raffinierter Antipasti.</dd>
  </dl>
  <div class="band" style="left:289px;top:368px;width:596px;height:19px"></div>
</section>

<!-- Spread: Rückseite und Titel -->
<section class="spread" style="left:22px;top:2822px;background:linear-gradient(90deg,#d6d8db,#f4f5f6 30%,#fff 50%)" aria-label="Rückseite und Titelseite">
  <div class="band" style="left:12px;top:47px;width:548px;height:309px;background:linear-gradient(90deg,#88ad09,var(--green))"></div>
  <div class="abs" style="left:12px;top:83px;width:218px;height:34px;background:#fff"></div>
  <div class="logo" style="left:246px;top:170px;font-size:18px;color:#fff"><span class="mark" style="background:#fff"></span>NORVENTA</div>
  <div class="contact" style="left:155px;top:238px"><b>NORVENTA</b>Lindenweg 12<br>40210 Düsseldorf<br><br><b>BÜROZEITEN</b>Mo.-Fr. 08:00 - 20:00</div>
  <div class="contact" style="left:283px;top:238px"><b>TELEFON</b>0800 1 234 567<br><br><br><b>EMAIL</b>info@norventa.de</div>

  <div class="page-cover" style="left:573px;top:0;transform:scale(.938,.925);transform-origin:0 0" aria-label="Titelseite">
    <div class="logo" style="left:47px;top:52px;font-size:20px"><span class="mark"></span>NORVENTA</div>
    <div class="year" style="right:18px;top:36px"><b>2018</b>DIE MODERNE<br>ART DES MIETENS</div>
    <div class="photo" role="img" aria-label="Fassade eines modernen Bürogebäudes" style="left:0;top:127px;width:315px;height:194px;background:linear-gradient(90deg,#e6dfd3,var(--photo-warm) 60%,#b9ae9c);clip-path:polygon(0 0,100% 0,72% 100%,0 100%)"></div>
    <div class="band" style="left:193px;top:168px;width:434px;height:110px;clip-path:polygon(12% 0,100% 0,100% 100%,0 100%);display:flex;align-items:center;padding-left:100px">
      <h1 class="cover-title">NEUE MAßSTÄBE<br>SETZEN</h1>
    </div>
    <p class="lead" style="left:385px;top:294px;width:210px">Unser modernes Business Center bietet mehr als ein reines Callcenter. Anrufannahme, hochwertigste Mietbüros und ein stylischer Konferenzraum</p>
    <p class="url" style="top:381px">www.buero-norventa.de</p>
  </div>
</section>

</body>
</html>
```